Dynamic Business Card for Sports Supplements Company

Hi! I'm looking for an awesome business card to match my existing sports supplement company. I have uploaded my current company logo and screenshot of the front page of my website.

I would like to have something dynamic and interesting and utilize the colors in the website - the reds and purples

The business card should be double sided and focus on a unique eye-catching design on the back and include all the relevant company info.

Most importantly, it should say somewhere: "Sign up on our website for a coupon code."

Target Market(s)

Mostly for women gym goers but it shouldn't be too feminine. It should be in keeping with the website design. It should flow and clearly be connected to it

Industry/Entity Type

Business

Contact Information for Business Card

Lorraine K. Vestal
CEO
LVestal@Quorvanexco.com
www.quorvanexco.com
555.417.3820
P.O. Box 47315
Harlow, Ohio 00000

Sign up on our website for a coupon code

Font styles to use
Serif
Sans Serif
Other font styles liked:
• Novecento font family and "Quorvanex" is in AR Destine font

Requirements
Must have
• One side should be a bold Quorvanex logo design. Even just the symbol itself may be o.k. (see attached file)

```html
<!DOCTYPE html>
<html lang="en">
<head>
<meta charset="utf-8">
<title>Quorvanex Business Card</title>
<link rel="stylesheet" href="https://fonts.googleapis.com/css2?family=PT+Sans:wght@400;700&family=Saira:wght@700&display=swap">
<style>
  :root {
    --stage: #c2c2c2;
    --slate-top: #343a48;
    --slate-bottom: #1e2330;
    --purple-top: #4a3f9a;
    --purple-bottom: #2b2564;
    --accent-red: #ec1c24;
    --ink-white: #ffffff;
    --ink-muted: #c9cbd2;
  }
  * { box-sizing: border-box; margin: 0; padding: 0; }
  html, body { width: 1200px; height: 900px; overflow: hidden; }
  body {
    position: relative;
    background: var(--stage);
    font-family: "PT Sans", Arial, sans-serif;
  }
  .card {
    position: absolute;
    top: 271px;
    width: 458px;
    height: 282px;
    border-radius: 14px;
    overflow: hidden;
    box-shadow: 0 2px 4px rgba(0,0,0,0.35);
  }
  .card--front {
    left: 137px;
    background: linear-gradient(160deg, var(--slate-top), var(--slate-bottom));
  }
  .card--back {
    left: 626px;
    background: linear-gradient(160deg, var(--purple-top), var(--purple-bottom));
  }
  .brand-ring {
    position: absolute;
    left: 38px;
    top: 56px;
    width: 144px;
    height: 144px;
    border: 5px solid var(--ink-white);
    border-radius: 50%;
    display: flex;
    align-items: center;
    justify-content: center;
    color: var(--ink-white);
    font-weight: 700;
    font-size: 20px;
    letter-spacing: 0.5px;
  }
  .contact {
    position: absolute;
    left: 236px;
    top: 63px;
    color: var(--ink-white);
  }
  .contact__name {
    font-size: 17px;
    font-weight: 400;
    text-transform: uppercase;
    letter-spacing: 0.3px;
    line-height: 20px;
  }
  .contact__title {
    font-size: 12px;
    color: var(--ink-muted);
    margin: 2px 0 0 4px;
  }
  .contact__list {
    list-style: none;
    margin: 10px 0 0 4px;
  }
  .contact__item {
    display: flex;
    align-items: center;
    gap: 6px;
    font-size: 13px;
    line-height: 20.5px;
    color: var(--ink-muted);
  }
  .contact__icon { width: 11px; height: 11px; fill: var(--accent-red); }
  .contact__address {
    font-style: normal;
    font-size: 13px;
    line-height: 17px;
    color: var(--ink-muted);
    margin: 10px 0 0 4px;
  }
  .back-brand {
    position: absolute;
    left: 0;
    width: 368px;
    top: 168px;
    text-align: center;
    color: var(--ink-white);
  }
  .back-brand__name {
    font-family: "Saira", Arial, sans-serif;
    font-weight: 700;
    font-size: 31px;
    letter-spacing: 1.5px;
    line-height: 32px;
  }
  .back-brand__tagline {
    font-size: 11px;
    letter-spacing: 1.6px;
    text-transform: uppercase;
    line-height: 13px;
  }
  .promo-corner {
    position: absolute;
    left: 0; top: 0;
    width: 458px; height: 282px;
  }
  .promo-text {
    position: absolute;
    left: 334px;
    top: 192px;
    width: 120px;
    transform: rotate(-47deg);
    transform-origin: center;
    text-align: center;
    color: var(--ink-white);
    font-weight: 700;
    font-size: 12.5px;
    line-height: 14px;
    text-transform: uppercase;
  }
</style>
</head>
<body>
  <section class="card card--front">
    <div class="brand-ring">Quorvanex</div>
    <div class="contact">
      <h1 class="contact__name">Lorraine K. Vestal</h1>
      <p class="contact__title">CEO</p>
      <ul class="contact__list">
        <li class="contact__item">
          <svg class="contact__icon" viewBox="0 0 12 12"><path d="M1 3c0-1 1-2 2-2h1l1 2-1 1c1 2 2 3 4 4l1-1 2 1v1c0 1-1 2-2 2C5 11 1 7 1 3z"/></svg>
          555.417.3820
        </li>
        <li class="contact__item">
          <svg class="contact__icon" viewBox="0 0 12 12"><path d="M0 2h12v1L6 7 0 3z"/><path d="M0 4.5l6 4 6-4V10H0z"/></svg>
          LVestal@Quorvanexco.com
        </li>
        <li class="contact__item">
          <svg class="contact__icon" viewBox="0 0 12 12"><circle cx="6" cy="6" r="5.5"/></svg>
          www.quorvanexco.com
        </li>
      </ul>
      <address class="contact__address">P.O. Box 47315<br>Harlow, Ohio 00000</address>
    </div>
  </section>

  <section class="card card--back">
    <div class="back-brand">
      <p class="back-brand__name">QUORVANEX</p>
      <p class="back-brand__tagline">Your Performance Partner</p>
    </div>
    <svg class="promo-corner" viewBox="0 0 458 282" aria-hidden="true">
      <polygon points="275,282 458,109 458,282" fill="var(--accent-red)"/>
    </svg>
    <p class="promo-text">Sign up on our website for a coupon code</p>
  </section>
</body>
</html>
```